Realty Group Needs Classy, Contemporary Letterhead Design

We need a letterhead design for a new realty company located in NY, USA. We buy investment properties to rehabilitate and or keep in our rental portfolio.

```html
<!DOCTYPE html>
<html lang="en">
<head>
<meta charset="UTF-8">
<title>Alderway Realty Group – Letterhead</title>
<link href="https://fonts.googleapis.com/css2?family=Montserrat:wght@400;500;700;800&display=swap" rel="stylesheet">
<style>
  :root {
    --backdrop: #c9c9c9;
    --paper: #ffffff;
    --brand-purple: #5c3d8f;
    --text-grey: #4a4a4a;
  }
  html, body {
    margin: 0;
    padding: 0;
    width: 1200px;
    height: 900px;
    overflow: hidden;
    background: var(--backdrop);
    font-family: "Montserrat", sans-serif;
  }
  .letterhead {
    position: absolute;
    left: 275px;
    top: 30px;
    width: 649px;
    height: 840px;
    background: var(--paper);
    box-shadow: 0 10px 28px rgba(0,0,0,0.22);
  }
  .brand {
    position: absolute;
    left: 43px;
    top: 76px;
    display: flex;
    align-items: center;
    gap: 10px;
  }
  .brand-dot {
    width: 16px;
    height: 16px;
    border-radius: 50%;
    background: var(--brand-purple);
  }
  .brand-name {
    font-weight: 800;
    font-size: 26px;
    letter-spacing: 0.2px;
    color: var(--brand-purple);
  }
  .footer-bar {
    position: absolute;
    left: 0;
    top: 696px;
    width: 9px;
    height: 102px;
    background: var(--brand-purple);
  }
  .contact {
    position: absolute;
    left: 43px;
    top: 693px;
    color: var(--text-grey);
    font-size: 12.5px;
    line-height: 17px;
  }
  .address {
    margin: 0;
  }
  .divider {
    width: 20px;
    height: 2px;
    background: var(--brand-purple);
    margin: 9px 0 14px;
  }
  .contact-list {
    list-style: none;
    margin: 0;
    padding: 0;
  }
  .contact-list li {
    display: flex;
    align-items: center;
    gap: 5px;
  }
  .contact-list svg {
    width: 8px;
    height: 8px;
    flex: none;
  }
</style>
</head>
<body>
  <div class="letterhead">
    <div class="brand">
      <span class="brand-dot"></span>
      <span class="brand-name">Alderway Realty Group, LLC</span>
    </div>

    <div class="footer-bar"></div>
    <div class="contact">
      <p class="address">2870 Linden Street<br>Brooklyn, NY 11221</p>
      <div class="divider"></div>
      <ul class="contact-list">
        <li>
          <svg viewBox="0 0 10 10" aria-hidden="true"><path d="M2 1 L4 1 L4.6 3 L3.4 4 Q4.5 6 6 6.6 L7 5.4 L9 6 L9 8 Q8.5 9 7.5 9 Q1 8 1 2.5 Q1 1 2 1 Z" fill="var(--brand-purple)"/></svg>
          <span>+1 555 0148-2210</span>
        </li>
        <li>
          <svg viewBox="0 0 10 10" aria-hidden="true"><rect x="0.8" y="2" width="8.4" height="6" fill="none" stroke="var(--brand-purple)" stroke-width="1.2"/><path d="M1 2.3 L5 5.3 L9 2.3" fill="none" stroke="var(--brand-purple)" stroke-width="1.1"/></svg>
          <span>info@alderwayrealtygroup.com</span>
        </li>
        <li>
          <svg viewBox="0 0 10 10" aria-hidden="true"><circle cx="5" cy="5" r="4.2" fill="none" stroke="var(--brand-purple)" stroke-width="1.1"/><ellipse cx="5" cy="5" rx="1.8" ry="4.2" fill="none" stroke="var(--brand-purple)" stroke-width="0.9"/><line x1="0.8" y1="5" x2="9.2" y2="5" stroke="var(--brand-purple)" stroke-width="0.9"/></svg>
          <span>www.alderwayrealtygroup.com</span>
        </li>
      </ul>
    </div>
  </div>
</body>
</html>
```